BUSINESS CARD DESIGN

NAME- DALE VORSKIN
PHONE NUMER - 555- 714-9082
EMAIL- OFFICE@TRV-GROUNDMAKRZ.COM
BACK OF CARD- SPEACIALIZES IN LAND CLEARING, FORESTRY MUCLHING AND EXCAVATION

Contact Information for Business Card

NAME- DALE VORSKIN PHONE NUMER - 555- 714-9082 EMAIL- OFFICE@TRV-GROUNDMAKRZ.COM BACK OF CARD- SPEACIALIZES IN LAND CLEARING , MUCLHING AND EXCAVATION

```html
<!DOCTYPE html>
<html lang="en">
<head>
<meta charset="utf-8">
<title>Traverse Ground Makrz – Business Card</title>
<link rel="stylesheet" href="https://fonts.googleapis.com/css2?family=Roboto:wght@300;400;700&display=swap">
<style>
  :root {
    --page-bg: #e3e7e8;
    --card-bg: #222226;
    --card-mark: #28282d;
    --accent: #f5b21b;
    --contact: #ececec;
  }
  * { margin: 0; padding: 0; box-sizing: border-box; }
  html, body {
    width: 1200px; height: 960px; overflow: hidden;
    background: var(--page-bg);
    font-family: "Roboto", Arial, sans-serif;
  }
  .card {
    position: absolute; left: 250px; width: 702px; height: 400px;
    background: var(--card-bg);
    border-bottom: 3px solid var(--accent);
    overflow: hidden;
  }
  .card--front { top: 60px; }
  .card--back { top: 500px; }

  .brand-mark {
    position: absolute; left: 351px; top: 140px; transform: translate(-50%, -50%);
    width: 150px; height: 150px; border-radius: 50%;
    border: 6px solid var(--accent);
  }
  .brand-name {
    position: absolute; left: 0; right: 0; top: 238px;
    text-align: center; color: var(--accent);
    font-weight: 700; font-size: 22px; letter-spacing: 1px;
  }
  .brand-rule {
    position: absolute; left: 209px; width: 284px; top: 299px;
    height: 2px; background: var(--accent);
  }
  .brand-phone {
    position: absolute; left: 0; right: 0; top: 303px;
    text-align: center; color: var(--accent);
    font-weight: 700; font-size: 13px; letter-spacing: 11px; text-indent: 11px;
  }
  .tagline {
    position: absolute; left: 0; right: 0; top: 356px;
    text-align: center; color: var(--accent);
    font-weight: 400; font-size: 16px; letter-spacing: 0.3px;
  }

  .back-mark {
    position: absolute; left: 348px; top: 218px; transform: translate(-50%, -50%);
    width: 420px; height: 420px; border-radius: 50%;
    border: 14px solid var(--card-mark);
  }
  .holder-name {
    position: absolute; left: 0; right: 0; top: 156px;
    text-align: center; color: var(--accent);
    font-size: 46px; letter-spacing: 1px; line-height: 1;
  }
  .holder-name__first { font-weight: 700; }
  .holder-name__last { font-weight: 300; }
  .contact-list {
    position: absolute; left: 0; right: 0; top: 248px;
    list-style: none; text-align: center; color: var(--contact);
    font-weight: 400; font-size: 16px; line-height: 22.5px; letter-spacing: 0.5px;
  }
</style>
</head>
<body>
  <section class="card card--front">
    <div class="brand-mark"></div>
    <div class="brand-name">TRAVERSE GROUND MAKRZ LLC</div>
    <div class="brand-rule"></div>
    <div class="brand-phone">555-714-9082</div>
    <p class="tagline">SPEACIALIZES IN LAND CLEARING , MUCLHING AND EXCAVATION</p>
  </section>

  <section class="card card--back">
    <div class="back-mark"></div>
    <h1 class="holder-name"><span class="holder-name__first">DALE</span> <span class="holder-name__last">VORSKIN</span></h1>
    <ul class="contact-list">
      <li>555- 714-9082</li>
      <li>WWW.TRV-GROUNDMAKRZ.COM</li>
      <li>OFFICE@TRV-GROUNDMAKRZ.COM</li>
    </ul>
  </section>
</body>
</html>
```